Flyer für ambulanten Pflegedienst
Zielgruppe
Ambulanter Pflegedienst, Potentielle Kunden für Grund- und Behandlungspflege, nicht nur Pflegebedürftige, sondern auch Angehörige. Flyer dient zur Auslage, beispielsweise in Wartezimmern von Ärzten.
Aufgabenstellung
Ausführliches Briefing mit Aufbau und Text in der Anlage, ebenso das Bildmaterial, Fonts, Logos. Flyer in A4 Wickelfalz, bitte die Gestaltungsvorlage mit den Maßen des Druckanbieters (ebenfalls anbei) beachten. Vorerst hauptsächlich KI-generierte/Stockfotos vorhanden, Fotoshooting folgt im Juli und Bilder werden dann ggf. nochmal ersetzt um persönliche Ebene zu erzeugen. Der erste Wurf muss aber vorerst so erfolgen. Übergabe der Daten: Druckfähiges PDF, PDF mit Ebenen und AI

```html
<!DOCTYPE html>
<html lang="de">
<head>
<meta charset="utf-8">
<title>Wendt Pflege – Flyer Wickelfalz</title>
<link href="https://fonts.googleapis.com/css2?family=Nunito:wght@700;800;900&family=Inter:wght@400;500;600;700&display=swap" rel="stylesheet">
<style>
:root{
  --bg:#ebebeb;
  --navy:#1e3784;
  --blue:#2346a3;
  --sky:#2aa9ec;
  --green:#0f7a3b;
  --green-text:#127a3a;
  --mint:#7fd39a;
  --ink:#2b2b2b;
  --muted:#5a5f6b;
  --card:#eef0f4;
  --white:#ffffff;
}
*{box-sizing:border-box;margin:0;padding:0}
html,body{width:871px;height:1200px;overflow:hidden;background:var(--bg)}
body{position:relative;font-family:"Inter",Arial,sans-serif;color:var(--ink)}
.sheet{position:absolute;left:70px;width:732px;height:517px;background:var(--white);box-shadow:0 6px 14px rgba(0,0,0,.18);overflow:hidden}
.sheet--outside{top:65px}
.sheet--inside{top:617px}
.panel{position:absolute;top:0;height:517px;overflow:hidden}
.abs{position:absolute}
.eyebrow{font-size:7.6px;letter-spacing:.9px;font-weight:500;text-transform:uppercase}
.headline{font-family:"Nunito",Arial,sans-serif;font-weight:900;line-height:1.06}
.copy{font-size:7.6px;line-height:1.38}
.brand{font-family:"Inter",Arial,sans-serif;font-weight:700;display:flex;align-items:center;gap:5px;white-space:nowrap}
.brand .dot{width:10px;height:10px;border-radius:50%;display:inline-block;flex:none}
.photo{position:absolute}
.small{font-size:6.6px;line-height:1.5;white-space:nowrap}

.p-a{left:0;width:238px;background:var(--white)}
.p-a .eyebrow{color:var(--sky);left:21px;top:26px}
.p-a .headline{left:21px;top:39px;font-size:17.5px;color:var(--navy);width:205px}
.p-a .copy{left:21px;width:193px}
.p-a .bottom{left:0;top:270px;width:238px;height:247px;background:linear-gradient(180deg,#2b4aa6 0%,#20409a 100%)}
.contact-line{display:flex;align-items:center;gap:3px;font-size:6.8px;color:var(--white);height:12.5px;white-space:nowrap}
.contact-line svg{flex:none}

.p-b{left:238px;width:247px;background:var(--white)}
.p-b .eyebrow{left:25px;top:125px;color:#4c4f56;font-size:7.8px}
.p-b .headline{left:25px;top:140px;font-size:16.5px;color:var(--green-text)}
.service{position:absolute;left:25px;width:210px;display:flex;gap:13px}
.service .txt{font-size:7.6px;line-height:1.38}
.service b{color:var(--green-text);font-weight:600}

.p-c{left:485px;width:247px}
.stat{position:absolute;top:479px;width:70px;text-align:center;font-size:7.2px;font-weight:700;color:var(--white);line-height:1.25}

.p-d{left:0;width:247px;background:var(--blue)}
.p-e{left:247px;width:246px;background:linear-gradient(90deg,#fff 0%,#f8f9fb 100%)}
.p-f{left:493px;width:239px;background:var(--white)}

.card{position:absolute;width:197px;height:84px;background:var(--card)}
.card .icon{position:absolute;left:11px;top:10px}
.card h3{position:absolute;left:57px;font-family:"Nunito",Arial,sans-serif;font-weight:900;font-size:10.5px;color:var(--navy);line-height:1.15}
.card p{position:absolute;left:12px;right:10px;top:53px;font-size:6.9px;line-height:1.5;color:var(--muted)}
</style>
</head>
<body>

<section class="sheet sheet--outside">

  <div class="panel p-a">
    <p class="abs eyebrow">Was uns besonders macht</p>
    <h2 class="abs headline">Pflege braucht Vertrau-<br>en. Und Menschen, die<br>da sind.</h2>
    <p class="abs copy" style="top:105px">Gute Pflege entsteht durch Aufmerksamkeit,<br>Erfahrung und ein verlässliches Team.</p>
    <p class="abs copy" style="top:131px">Bei der Hauskrankenpflege Wendt arbeiten engagierte Pflegekräfte, Betreuungskräfte und Fachpersonen Hand in Hand – mit Herz, Respekt und fachlicher Kompetenz. Über 40 Mitarbeitende geben Tag für Tag ihr Bestes für Sie und Ihre Angehörigen.</p>

    <div class="abs bottom"></div>
    <div class="photo" role="img" aria-label="Foto: Pflegekraft in blauer Kleidung legt einer älteren Dame lächelnd eine Decke um" style="left:0;top:200px;width:238px;height:180px;background:linear-gradient(180deg,#b9a895 0%,#9c8d85 40%,#5c6aa4 78%,#2a48a4 100%);border-top-right-radius:120px 70px"></div>
    <svg class="abs" style="left:0;top:190px" width="238" height="190" viewBox="0 0 238 190">
      <path d="M0 60 C60 0 200 -10 238 60 L238 70 C215 10 90 10 0 75 Z" fill="var(--blue)"/>
      <path d="M228 40 C250 100 240 150 190 190 L200 190 C245 150 252 95 232 40 Z" fill="var(--blue)"/>
    </svg>

    <p class="abs headline" style="left:21px;top:358px;font-size:11.5px;color:var(--sky);font-weight:800">Wir sind für Sie da.</p>
    <p class="abs copy" style="top:377px;color:var(--white)">Sie möchten sich informieren oder ein persönliches Gespräch vereinbaren? Wir beraten Sie gerne – unkompliziert, persönlich und unverbindlich.</p>

    <div class="abs brand" style="left:21px;top:434px;font-size:11px;color:var(--white)"><span class="dot" style="background:var(--sky)"></span>Wendt Pflege</div>

    <div class="abs" style="left:135px;top:420px">
      <div class="contact-line" style="font-weight:700"><svg width="7" height="7" viewBox="0 0 10 10"><path d="M2 1 L4 1 L5 3.5 L3.8 4.5 C4.5 6 5 6.5 6.5 7.2 L7.5 6 L10 7 L10 9 C5 10 0 5 2 1Z" fill="var(--sky)"/></svg>0 12 34 - 56 78 0</div>
      <div class="contact-line"><svg width="7" height="6" viewBox="0 0 10 8"><rect width="10" height="8" rx="1" fill="var(--sky)"/><path d="M0 1 L5 5 L10 1" stroke="#2346a3" fill="none"/></svg>info@wendt-pflege.de</div>
      <div class="contact-line"><svg width="7" height="7" viewBox="0 0 10 10"><circle cx="5" cy="5" r="4.3" fill="none" stroke="var(--sky)" stroke-width="1.2"/><path d="M1 5h8M5 1v8" stroke="var(--sky)"/></svg>www.wendt-pflege.de</div>
    </div>

    <div class="abs" style="left:21px;top:466px;width:96px;height:1px;background:rgba(255,255,255,.35)"></div>
    <p class="abs small" style="left:21px;top:475px;color:var(--white)"><b style="font-weight:700">Hauskrankenpflege Wendt</b><br>Am Markt 10 · 12345 Feldheim</p>
    <p class="abs small" style="left:135px;top:468px;color:var(--white);line-height:1.4"><span style="color:var(--sky)">Bürozeiten:</span><br>Mo., Di., Mi., Fr. 9 bis 12<br>Uhr und Do. 15 bis 17 Uhr</p>
  </div>

  <div class="panel p-b">
    <div class="photo" role="img" aria-label="Foto: lächelnde Haushaltshilfe in grünem Shirt mit Putzmitteln, heller Hintergrund" style="left:0;top:0;width:247px;height:185px;background:linear-gradient(180deg,#9aa9a4 0%,#c4cdc8 55%,#ffffff 100%)"></div>
    <div class="abs" style="left:0;top:120px;width:247px;height:65px;background:linear-gradient(180deg,rgba(255,255,255,.55),rgba(255,255,255,.95))"></div>
    <div class="abs brand" style="left:25px;top:34px;font-size:11px;color:var(--green)"><span class="dot" style="background:var(--green)"></span>Wendt Hausdienste</div>
    <p class="abs eyebrow">Hauswirtschaftliche Versorgung</p>
    <h2 class="abs headline">Hilfe im Haushalt.<br>Entlastung im Alltag.</h2>
    <div class="abs" style="left:25px;top:181px;width:222px;height:1px;background:#d4d7d6"></div>
    <p class="abs copy" style="left:25px;top:187px;width:200px">Damit Sie sich zuhause weiterhin wohlfühlen können, bieten über 25 Kolleginnen im Team der Wendt Hausdienste fachgerechte und zuverlässige Unterstützung in verschiedenen Bereichen:</p>

    <div class="service" style="top:236px">
      <svg width="28" height="24" viewBox="0 0 28 24"><circle cx="14" cy="13" r="10" fill="none" stroke="var(--green)" stroke-width="1.6"/><path d="M9 13 L13 17 L20 9" stroke="var(--green)" stroke-width="2" fill="none"/></svg>
      <div class="txt"><b>Hilfe im Haushalt</b><br>Unterstützung bei alltäglichen Aufgaben – von der Grundreinigung bis zur Wäschepflege.</div>
    </div>
    <div class="service" style="top:286px">
      <svg width="28" height="24" viewBox="0 0 28 24"><circle cx="14" cy="13" r="10" fill="none" stroke="var(--green)" stroke-width="1.6"/><circle cx="11" cy="10" r="2.3" fill="var(--green)"/><circle cx="17" cy="10" r="2.3" fill="var(--green)"/><path d="M7 18 C8 13 14 13 14 18 Z M14 18 C14 13 20 13 21 18Z" fill="var(--green)"/></svg>
      <div class="txt"><b>Alltagsbegleitung</b><br>Niemand ist gern allein und wir sind für Sie da, wenn Sie Gesellschaft wünschen.</div>
    </div>
    <div class="service" style="top:325px">
      <svg width="28" height="24" viewBox="0 0 28 24"><circle cx="14" cy="13" r="10" fill="none" stroke="var(--green)" stroke-width="1.6"/><path d="M14 17 C8 13 10 8 14 11 C18 8 20 13 14 17Z" fill="var(--green)"/></svg>
      <div class="txt"><b>Betreuung</b><br>Strukturierte Betreuung und Hilfe nach individuellem Bedarf.</div>
    </div>

    <svg class="abs" style="left:0;top:368px" width="247" height="149" viewBox="0 0 247 149" preserveAspectRatio="none"><path d="M0 0 C90 2 180 6 247 15 L247 149 L0 149Z" fill="var(--green)"/></svg>
    <p class="abs headline" style="left:25px;top:383px;font-size:11.5px;color:var(--mint);font-weight:800">So erreichen Sie uns</p>
    <p class="abs copy" style="left:25px;top:402px;width:200px;color:var(--white)">Das Team der Wendt Hausdienste steht Ihnen bei Fragen und Terminwünschen gern zur Verfügung:</p>
    <p class="abs small" style="left:25px;top:432px;color:var(--white)"><b style="font-weight:700">Wendt Hausdienste GmbH</b><br>Am Markt 10 · 12345 Feldheim</p>
    <div class="abs" style="left:25px;top:461px">
      <div class="contact-line" style="font-weight:700"><svg width="7" height="7" viewBox="0 0 10 10"><path d="M2 1 L4 1 L5 3.5 L3.8 4.5 C4.5 6 5 6.5 6.5 7.2 L7.5 6 L10 7 L10 9 C5 10 0 5 2 1Z" fill="var(--mint)"/></svg>0 12 34 - 98 76 543</div>
      <div class="contact-line"><svg width="7" height="6" viewBox="0 0 10 8"><rect width="10" height="8" rx="1" fill="var(--mint)"/><path d="M0 1 L5 5 L10 1" stroke="#0f7a3b" fill="none"/></svg>info@wendt-hausdienste.de</div>
      <div class="contact-line"><svg width="7" height="7" viewBox="0 0 10 10"><circle cx="5" cy="5" r="4.3" fill="none" stroke="var(--mint)" stroke-width="1.2"/><path d="M1 5h8M5 1v8" stroke="var(--mint)"/></svg>www.wendt-hausdienste.de</div>
    </div>
    <div class="abs" style="left:141px;top:436px;width:1px;height:60px;background:rgba(255,255,255,.3)"></div>
    <div class="abs brand" style="left:159px;top:441px;font-size:7px;gap:4px;color:var(--white)"><span class="dot" style="background:var(--mint);width:7px;height:7px"></span>Wendt Hausdienste</div>
    <p class="abs small" style="left:159px;top:466px;color:var(--white);line-height:1.4"><span style="color:var(--mint)">Bürozeiten:</span><br>Mo., Di., Do., Fr.<br>8 bis 11 Uhr</p>
  </div>

  <div class="panel p-c">
    <div class="photo" role="img" aria-label="Foto: lächelnde Pflegekraft im blauen Poloshirt im Gespräch mit einer älteren Dame in einem hellen Wohnzimmer" style="left:0;top:0;width:247px;height:517px;background:linear-gradient(180deg,#e9e4de 0%,#cbbdae 30%,#7a6f86 52%,#3a4f9f 68%,#2346a3 100%)"></div>
    <div class="abs brand" style="left:66px;top:42px;font-size:13px;color:var(--navy)"><span class="dot" style="background:var(--navy);width:12px;height:12px"></span>Wendt Pflege</div>
    <h1 class="abs headline" style="left:25px;top:298px;font-size:23px;color:var(--white);line-height:1.02">Weil das eigene<br>Zuhause<br>Lebensqualität ist.</h1>
    <p class="abs headline" style="left:25px;top:380px;font-size:12.5px;color:var(--sky);font-weight:800;line-height:1.25">Ihr ambulanter Pflegedienst<br>für die Region.</p>
    <div class="abs" style="left:25px;top:419px;width:16px;height:1px;background:var(--white)"></div>
    <p class="abs copy" style="left:25px;top:433px;width:206px;font-size:7.4px;color:var(--white)">Seit über 30 Jahren begleiten wir Menschen im Raum Feldheim und Umgebung in ihrem vertrauten Zuhause – individuell, menschlich und mit fachlicher Kompetenz.</p>
    <div class="stat" style="left:15px">24h<br>erreichbar</div>
    <div class="abs" style="left:81px;top:477px;width:1px;height:17px;background:var(--sky)"></div>
    <div class="stat" style="left:89px">Persönliche<br>Beratung</div>
    <div class="abs" style="left:161px;top:477px;width:1px;height:17px;background:var(--sky)"></div>
    <div class="stat" style="left:169px">MD-geprüfte<br>Qualität</div>
  </div>
</section>

<section class="sheet sheet--inside">

  <div class="panel p-d">
    <p class="abs eyebrow" style="left:25px;top:26px;color:var(--white)">Wer wir sind</p>
    <h2 class="abs headline" style="left:25px;top:39px;font-size:17.5px;color:var(--sky)">Vertrauen beginnt mit<br>Zuhören.</h2>
    <p class="abs copy" style="left:25px;top:88px;width:198px;color:var(--white)">Pflege bedeutet für uns mehr als Versorgung. Es geht um Menschen, ihre Gewohnheiten, ihre Wünsche und das gute Gefühl, in den eigenen vier Wänden bleiben zu können.</p>
    <p class="abs copy" style="left:25px;top:134px;width:198px;color:var(--white)">Deshalb nehmen wir uns Zeit für persönliche Gespräche und individuelle Lösungen. Gemeinsam mit unseren Kundinnen, Kunden und Angehörigen gestalten wir eine Unterstützung, die zum Leben passt – nicht umgekehrt.</p>
    <p class="abs copy" style="left:25px;top:191px;width:198px;color:var(--white)">Als ambulanter Pflegedienst begleiten wir Menschen im Raum Feldheim und Umgebung zuverlässig im Alltag und stehen auch Angehörigen beratend zur Seite.</p>
    <div class="abs" style="left:25px;top:236px;width:3px;height:42px;background:var(--sky)"></div>
    <p class="abs headline" style="left:40px;top:235px;font-size:12px;color:var(--white);font-weight:800;line-height:1.24">„Unsere Pflege orientiert sich<br>am Befinden der Menschen<br>– nicht am Befund.“</p>
    <div class="photo" role="img" aria-label="Foto: zwei Pflegekräfte in blauen Poloshirts begleiten eine ältere Dame Arm in Arm neben einem weißen Auto im Grünen" style="left:0;top:279px;width:247px;height:238px;background:linear-gradient(180deg,#2346a3 0%,#4f6a6c 22%,#6f8a5a 45%,#3d4f7e 75%,#2b3c73 100%)"></div>
    <div class="abs brand" style="left:5px;top:498px;font-size:10px;color:var(--white)"><span class="dot" style="background:var(--white)"></span>Wendt Pflege</div>
  </div>

  <div class="panel p-e">
    <p class="abs eyebrow" style="left:24px;top:26px;color:var(--sky)">Unsere Leistungen</p>
    <h2 class="abs headline" style="left:24px;top:39px;font-size:17.5px;color:var(--navy)">Unterstützung, die den<br>Alltag leichter macht.</h2>
    <p class="abs copy" style="left:24px;top:88px;width:195px">Jeder Mensch braucht etwas anderes. Deshalb richten wir unsere Leistungen individuell nach Ihrer persönlichen Situation aus.</p>

    <div class="card" style="left:24px;top:134px">
      <svg class="icon" width="36" height="28" viewBox="0 0 36 28"><ellipse cx="18" cy="14" rx="16" ry="12" fill="none" stroke="var(--blue)" stroke-width="1.8"/><path d="M18 20 C9 14 12 6 18 10 C24 6 27 14 18 20Z" fill="var(--blue)"/></svg>
      <h3 style="top:18px">Grundpflege</h3>
      <p>Unterstützung bei Körperpflege, Mobilität, Ernährung und allem, was Sicherheit im Alltag gibt.</p>
    </div>
    <div class="card" style="left:24px;top:227px">
      <svg class="icon" width="36" height="28" viewBox="0 0 36 28"><ellipse cx="18" cy="14" rx="16" ry="12" fill="none" stroke="var(--blue)" stroke-width="1.8"/><rect x="12" y="6" width="12" height="15" rx="1.5" fill="none" stroke="var(--blue)" stroke-width="1.6"/><path d="M15 11h6M15 14h6M15 17h4" stroke="var(--blue)" stroke-width="1.3"/></svg>
      <h3 style="top:18px">Behandlungspflege</h3>
      <p>Medizinische Versorgung nach ärztlicher Verordnung – zum Beispiel Wundversorgung, Medikamentengabe oder Injektionen.</p>
    </div>
    <div class="card" style="left:24px;top:320px">
      <svg class="icon" width="36" height="28" viewBox="0 0 36 28"><ellipse cx="18" cy="14" rx="16" ry="12" fill="none" stroke="var(--blue)" stroke-width="1.8"/><path d="M18 6 L24 8 L24 13 C24 17 21 19 18 21 C15 19 12 17 12 13 L12 8Z" fill="var(--blue)"/><path d="M15 13 L17.5 15.5 L21 11" stroke="#fff" stroke-width="1.4" fill="none"/></svg>
      <h3 style="top:12px">Betreuung<br>&amp; Alltagsbegleitung</h3>
      <p>Begleitung im Alltag, stundenweise Betreuung, Unterstützung bei Demenz sowie Entlastung für Angehörige.</p>
    </div>
    <div class="card" style="left:24px;top:414px">
      <svg class="icon" width="36" height="28" viewBox="0 0 36 28"><ellipse cx="18" cy="14" rx="16" ry="12" fill="none" stroke="var(--blue)" stroke-width="1.8"/><circle cx="21" cy="16" r="5" fill="none" stroke="var(--blue)" stroke-width="1.5"/><path d="M21 13.5 V16 H23" stroke="var(--blue)" stroke-width="1.3" fill="none"/><path d="M14 14 C8 10 10 5 14 8 C17 5 19 8 17 10" fill="var(--blue)"/></svg>
      <h3 style="top:18px">Verhinderungspflege</h3>
      <p>Auszeiten im Rahmen der Verhinderungspflege, denn auch pflegende Angehörige müssen mal durchatmen.</p>
    </div>
  </div>

  <div class="panel p-f">
    <div class="photo" role="img" aria-label="Foto: Pflegekraft in hellblauer Kleidung sitzt lächelnd neben einer älteren Dame auf dem Sofa, Pflanzen und Rollator im Hintergrund" style="left:18px;top:10px;width:221px;height:190px;border-radius:50% 0 0 50% / 50% 0 0 50%;background:linear-gradient(180deg,#8a9a7c 0%,#b9a996 45%,#8b98b4 80%,#5d77b8 100%)"></div>
    <svg class="abs" style="left:0;top:0" width="239" height="215" viewBox="0 0 239 215">
      <path d="M239 16 C150 20 50 60 26 115 C10 160 60 205 140 208 C185 210 220 200 239 190 L239 182 C215 193 180 200 140 198 C70 196 25 160 40 118 C60 70 150 30 239 26Z" fill="var(--blue)"/>
    </svg>

    <div class="card" style="left:21px;top:227px">
      <svg class="icon" width="36" height="28" viewBox="0 0 36 28"><ellipse cx="18" cy="14" rx="16" ry="12" fill="none" stroke="var(--blue)" stroke-width="1.8"/><rect x="12" y="7" width="13" height="11" rx="2" fill="var(--blue)"/><path d="M18.5 9.5v6M15.5 12.5h6" stroke="#fff" stroke-width="1.6"/></svg>
      <h3 style="top:18px">Beratung</h3>
      <p>Pflegeberatung nach § 37.3 SGB XI zur Sicherstellung des Pflegegeld-Bezugs, Unterstützung bei Anträgen und Hilfe bei allen Fragen rund um Pflegeleistungen.</p>
    </div>
    <div class="card" style="left:21px;top:320px">
      <svg class="icon" width="36" height="28" viewBox="0 0 36 28"><ellipse cx="18" cy="14" rx="16" ry="12" fill="none" stroke="var(--blue)" stroke-width="1.8"/><path d="M11 7 L14 7 L15.5 11 L13.8 12.4 C14.8 14.5 15.6 15.3 17.6 16.2 L19 14.5 L23 16 L23 19 C16 20.5 9 13 11 7Z" fill="var(--blue)"/><circle cx="21" cy="10" r="3.5" fill="var(--blue)"/><path d="M21 8.2v3.6M19.2 10h3.6" stroke="#fff" stroke-width="1.1"/></svg>
      <h3 style="top:12px">Hausnotruf<br>&amp; Erreichbarkeit</h3>
      <p>Sicherheit rund um die Uhr – mit einem Team, das erreichbar bleibt.</p>
    </div>
    <div class="card" style="left:21px;top:414px">
      <svg class="icon" width="36" height="28" viewBox="0 0 36 28"><ellipse cx="18" cy="14" rx="16" ry="12" fill="none" stroke="var(--blue)" stroke-width="1.8"/><circle cx="15" cy="8" r="2.2" fill="var(--blue)"/><path d="M13 11 h4 v5 h4 l2 4" stroke="var(--blue)" stroke-width="1.8" fill="none"/><circle cx="15" cy="19" r="3" fill="none" stroke="var(--blue)" stroke-width="1.4"/><path d="M24 5v5M21.5 7.5h5" stroke="var(--blue)" stroke-width="1.4"/></svg>
      <h3 style="top:18px">Palliative Versorgung</h3>
      <p>Als spezialisierter Anbieter ist uns die Versorgung und Begleitung zum Ende des Lebens ein besonderes Herzensanliegen.</p>
    </div>
  </div>
</section>

</body>
</html>
```